Modern business card design for professional copywriter

I'd like a business card design that I can use to have my cards printed out by quillprint.com as a squared corners business card (see artwork and design guidelines here: https://help.quillprint.com/hc/en-gb/sections/200570950-QUILL-Product-Templates)

The design should be clean and modern and reflect the colours, tone and branding on my website: https://tessavorrin.com.au

Target Market(s)

Professionals, B2B small business owners

Industry/Entity Type

Business

Contact Information for Business Card

Tessa Vorrin
m: 0468 905 327
e: tessa@tessavorrin.com.au
w: tessavorrin.com.au

Font styles to use
Sans Serif

Requirements
Must have
• Tagline: "Smart copywriting for clever business people"
• Brand colours: fd8000, 009984, 666666 and black
Nice to have

```html
<!DOCTYPE html>
<html lang="en">
<head>
<meta charset="utf-8">
<title>Tessa Vorrin – Business Card</title>
<link rel="stylesheet" href="https://fonts.googleapis.com/css2?family=Arimo&family=Questrial&display=swap">
<style>
  :root {
    --backdrop: #525252;
    --paper: #ffffff;
    --teal: #169b85;
    --orange: #f08323;
    --ink: #111111;
    --grey: #666666;
  }
  html, body {
    margin: 0;
    padding: 0;
    width: 1200px;
    height: 1200px;
    overflow: hidden;
    background: var(--backdrop);
  }
  .canvas {
    position: relative;
    width: 1200px;
    height: 1200px;
  }
  .card {
    position: absolute;
    width: 674px;
    height: 441px;
    box-sizing: border-box;
  }
  .card--front {
    left: 263px;
    top: 126px;
    background: var(--paper);
  }
  .card--back {
    left: 261px;
    top: 629px;
    background: var(--teal);
  }
  .brand {
    position: absolute;
    left: 0;
    right: 0;
    top: 178px;
    display: flex;
    justify-content: center;
    align-items: center;
    gap: 14px;
  }
  .brand__dot {
    width: 30px;
    height: 30px;
    border-radius: 50%;
    background: var(--orange);
  }
  .brand__name {
    font-family: "Questrial", sans-serif;
    font-size: 54px;
    line-height: 1;
    color: var(--teal);
    letter-spacing: -0.5px;
  }
  .tagline {
    position: absolute;
    left: 0;
    right: 0;
    margin: 0;
    text-align: center;
    font-family: "Arimo", sans-serif;
    font-size: 23px;
    line-height: 1;
  }
  .card--front .tagline {
    top: 322px;
    color: var(--ink);
    padding-left: 22px;
  }
  .card--back .tagline {
    top: 364px;
    color: var(--paper);
    padding-left: 14px;
  }
  .portrait {
    position: absolute;
    left: 95px;
    top: 135px;
    width: 168px;
    height: 168px;
    border-radius: 50%;
    border: 7px solid var(--paper);
    background: radial-gradient(circle at 50% 40%, #d9cfc4 0%, #b8aea6 55%, #6b6a66 100%);
  }
  .divider {
    position: absolute;
    left: 306px;
    top: 108px;
    width: 3px;
    height: 226px;
    background: var(--orange);
  }
  .contacts {
    position: absolute;
    left: 339px;
    top: 160px;
    margin: 0;
    padding: 0;
    list-style: none;
  }
  .contacts__item {
    display: flex;
    align-items: center;
    height: 28px;
    margin-bottom: 19px;
    font-family: "Questrial", sans-serif;
    font-size: 16px;
    letter-spacing: 0.6px;
    color: var(--paper);
  }
  .contacts__icon {
    width: 28px;
    height: 28px;
    margin-right: 21px;
    flex: none;
  }
</style>
</head>
<body>
<main class="canvas">
  <section class="card card--front" aria-label="Card front">
    <div class="brand">
      <span class="brand__dot"></span>
      <span class="brand__name">Tessa Vorrin</span>
    </div>
    <p class="tagline">Smart copywriting for clever business people</p>
  </section>

  <section class="card card--back" aria-label="Card back">
    <div class="portrait" role="img" aria-label="Portrait photograph of Tessa Vorrin"></div>
    <div class="divider"></div>
    <ul class="contacts">
      <li class="contacts__item">
        <svg class="contacts__icon" viewBox="0 0 28 28" aria-hidden="true">
          <circle cx="14" cy="14" r="14" fill="#fff"/>
          <path d="M9 7.5l3 0 1.2 3.6-1.8 1.4a9 9 0 0 0 4.1 4.1l1.4-1.8 3.6 1.2v3c0 .8-.7 1.5-1.5 1.5A12.5 12.5 0 0 1 7.5 9c0-.8.7-1.5 1.5-1.5z" fill="var(--orange)"/>
        </svg>
        0468 905 327
      </li>
      <li class="contacts__item">
        <svg class="contacts__icon" viewBox="0 0 28 28" aria-hidden="true">
          <circle cx="14" cy="14" r="14" fill="#fff"/>
          <g fill="none" stroke="var(--orange)" stroke-width="1.6">
            <circle cx="14" cy="14" r="7.5"/>
            <ellipse cx="14" cy="14" rx="3.2" ry="7.5"/>
            <line x1="6.5" y1="14" x2="21.5" y2="14"/>
            <line x1="8" y1="10" x2="20" y2="10"/>
            <line x1="8" y1="18" x2="20" y2="18"/>
          </g>
        </svg>
        tessavorrin.com.au
      </li>
      <li class="contacts__item">
        <svg class="contacts__icon" viewBox="0 0 28 28" aria-hidden="true">
          <circle cx="14" cy="14" r="14" fill="#fff"/>
          <rect x="7" y="9" width="14" height="10" fill="var(--orange)"/>
          <path d="M7 9l7 5.5L21 9M7 19l5-5M21 19l-5-5" fill="none" stroke="#fff" stroke-width="1"/>
        </svg>
        tessa@tessavorrin.com.au
      </li>
    </ul>
    <p class="tagline">Smart copywriting for clever business people</p>
  </section>
</main>
</body>
</html>
```